New Business Card for our Indoor Golf Training Facility

We are looking for designs for a new business card for our indoor golf training facility. Attached is our logo, our logo with our slogan, and here is our elevator pitch (What makes us different from the others) not sure if all the info will fit on one card, maybe you can condense the elevator pitch? here is the info

Elevator Pitch
We work with serious golfers and those that want to be serious golfers…
to make you better, faster, at all phases of the game…
We use the same state-of-the-art technology as professional golfers…
which produces data sets that shows your improvement in real time.
Our facility is available 24/7 to our members, which allows you to improve on your time.

our website: www.birchpinlinks.com

Target Market(s)

Golfers

Font styles to use
Serif
Sans Serif

Colors
ec1f27
f59195
fbd4d5
919191
d3d3d3
1b1b1b

Requirements
Must have
• our logo or our logo with the slogan, elevator pitch (can be condensed or shortened)

```html
<!DOCTYPE html>
<html lang="en">
<head>
<meta charset="utf-8">
<title>Birch Pin Links – Business Card</title>
<link href="https://fonts.googleapis.com/css2?family=Roboto:wght@400;500;700&family=Roboto+Condensed:wght@400;700&display=swap" rel="stylesheet">
<style>
  :root {
    --brand-red: #ec1f27;
    --red-soft: #f0463f;
    --red-light: #f59195;
    --pink-pale: #fbd4d5;
    --grey: #828282;
    --grey-light: #d3d3d3;
    --ink: #1b1b1b;
    --white: #ffffff;
    --paper: #f4f4f4;
    --stage: #e9e7e4;
  }
  * { box-sizing: border-box; margin: 0; padding: 0; }
  html, body { width: 1200px; height: 950px; overflow: hidden; }
  body {
    background: var(--stage);
    font-family: "Roboto", Arial, sans-serif;
    position: relative;
  }
  .card {
    position: absolute;
    left: 300px;
    width: 600px;
    height: 343px;
    border-radius: 18px;
    overflow: hidden;
    box-shadow: 0 6px 18px rgba(0,0,0,0.18);
  }
  .card--front { top: 100px; background: var(--paper); }
  .card--back  { top: 497px; background: var(--grey); color: var(--white); }

  .front-wave { position: absolute; inset: 0; width: 100%; height: 100%; }

  .brand {
    position: absolute;
    left: 30px;
    top: 152px;
    color: var(--brand-red);
  }
  .brand__row { display: flex; align-items: center; gap: 10px; }
  .brand__mark {
    width: 36px; height: 36px;
    border: 3px solid var(--brand-red);
    border-radius: 50%;
    flex: none;
  }
  .brand__name {
    font-size: 28px;
    font-weight: 700;
    letter-spacing: -0.3px;
    line-height: 1;
    white-space: nowrap;
  }
  .brand__slogan {
    margin-left: 47px;
    margin-top: 3px;
    font-size: 11.5px;
    font-weight: 400;
    white-space: nowrap;
  }

  .contact {
    position: absolute;
    right: 34px;
    top: 40px;
    text-align: right;
    color: var(--white);
  }
  .contact__name {
    font-size: 22px;
    font-weight: 700;
    text-transform: uppercase;
    letter-spacing: 0.5px;
  }
  .contact__title {
    font-size: 14px;
    font-weight: 400;
    margin-bottom: 18px;
  }
  .contact__line {
    font-size: 14px;
    line-height: 22px;
    display: flex;
    justify-content: flex-end;
    align-items: center;
    gap: 10px;
    white-space: nowrap;
  }
  .contact__icon { width: 14px; height: 14px; flex: none; }
  .contact__spacer { width: 14px; flex: none; }
  .contact__gap { height: 12px; }

  .pitch-mark {
    position: absolute;
    left: 250px;
    top: 28px;
    width: 100px;
    height: 100px;
    border: 5px solid var(--white);
    border-radius: 50%;
  }
  .pitch-title {
    position: absolute;
    left: 0; right: 0;
    top: 146px;
    text-align: center;
    font-size: 20px;
    font-weight: 700;
    letter-spacing: 0.5px;
  }
  .pitch-text {
    position: absolute;
    left: 30px; right: 30px;
    top: 186px;
    font-family: "Roboto Condensed", "Arial Narrow", sans-serif;
    font-size: 13.5px;
    line-height: 20px;
    text-align: center;
  }
  .social {
    position: absolute;
    left: 50%;
    transform: translateX(-50%);
    bottom: 22px;
    display: flex;
    gap: 8px;
  }
  .social__dot {
    width: 14px; height: 14px;
    border-radius: 50%;
    background: var(--white);
  }
</style>
</head>
<body>

  <section class="card card--front" aria-label="Business card front">
    <svg class="front-wave" viewBox="0 0 600 343" aria-hidden="true">
      <defs>
        <linearGradient id="redPanel" x1="0" y1="0" x2="0.3" y2="1">
          <stop offset="0" stop-color="#ec1f27"/>
          <stop offset="1" stop-color="#f0524c"/>
        </linearGradient>
      </defs>
      <path d="M412,0 C340,70 340,170 308,250 C292,292 288,320 286,343 L600,343 L600,0 Z" fill="#e8363a"/>
      <path d="M436,0 C370,70 370,170 338,250 C322,292 314,320 310,343 L600,343 L600,0 Z" fill="url(#redPanel)"/>
      <path d="M432,0 C366,70 366,170 334,250 C318,292 311,320 307,343" fill="none" stroke="#ffffff" stroke-width="5"/>
    </svg>

    <div class="brand">
      <div class="brand__row">
        <span class="brand__mark"></span>
        <span class="brand__name">Birch Pin Links</span>
      </div>
      <p class="brand__slogan">Play Smart. Train Hard. Be Better.</p>
    </div>

    <div class="contact">
      <p class="contact__name">Daniel Reyes</p>
      <p class="contact__title">CEO/FOUNDER</p>
      <p class="contact__line">4180 W. Alder Rd. Unit B4<span class="contact__spacer"></span></p>
      <p class="contact__line">Fairmont, OH 45390<span class="contact__spacer"></span></p>
      <div class="contact__gap"></div>
      <p class="contact__line">513-555-0172
        <svg class="contact__icon" viewBox="0 0 24 24" aria-hidden="true"><path fill="#fff" d="M6.6 10.8a15 15 0 0 0 6.6 6.6l2.2-2.2a1 1 0 0 1 1-.25 11.4 11.4 0 0 0 3.6.57 1 1 0 0 1 1 1V20a1 1 0 0 1-1 1A17 17 0 0 1 3 4a1 1 0 0 1 1-1h3.5a1 1 0 0 1 1 1c0 1.250.2 2.45.57 3.6a1 1 0 0 1-.25 1z"/></svg>
      </p>
      <p class="contact__line">info@birchpinlinks.com
        <svg class="contact__icon" viewBox="0 0 24 24" aria-hidden="true"><rect x="2" y="5" width="20" height="14" rx="2" fill="#fff"/><path d="M3 6l9 7 9-7" fill="none" stroke="#ec1f27" stroke-width="1.6"/></svg>
      </p>
      <p class="contact__line">www.birchpinlinks.com
        <svg class="contact__icon" viewBox="0 0 24 24" aria-hidden="true"><circle cx="12" cy="12" r="10" fill="#fff"/><path d="M2 12h20M12 2c3 3 3 17 0 20M12 2c-3 3-3 17 0 20" fill="none" stroke="#ec1f27" stroke-width="1.4"/></svg>
      </p>
    </div>
  </section>

  <section class="card card--back" aria-label="Business card back">
    <span class="pitch-mark"></span>
    <h2 class="pitch-title">ELEVATOR PITCH:</h2>
    <p class="pitch-text">
      We work with serious golfers and those that want to be serious golfers…<br>
      to make you better, faster, at all phases of the game…<br>
      We use the same state-of-the-art technology as professional golfers…<br>
      which produces data sets that shows your improvement in real time.<br>
      Our facility is available 24/7 to our members, which allows you to improve on your time.
    </p>
    <div class="social" aria-hidden="true">
      <span class="social__dot"></span>
      <span class="social__dot"></span>
    </div>
  </section>

</body>
</html>
```